Vantrel System Web Page Design

This project is to design 6 pages of a web based medical system for clinics, hospitals, drugs suppliers, general items suppliers, insurance company, laboratories and patients (basically all parties which could be involved in).We want the designs of the browser, button, icon and layout are based on Zeltor, which is user friendly, looks professional, simple and neat but with powerful functions. We have uploaded few pictures of another system, please do not copy its design because this is not what we are looking for, the pictures are for you to know the elements should be included in our pages. Vantrel web-base system, design 6 pages1. Login PageShould include the following elements-company id with input field-login id with input field-password with input field2. Main Page (Navigation page)Should include the following elements-Appointment-Consultation-Patient-Drugs inventory -General supplies inventory -Laboratory-Suppliers-Insurance-Reports 3. Appointment PageShould include all the the elements in the respective pictures plus the followings-Daily View, Weekly View, Monthly View buttons4. Consultation PageShould include all the the elements in the respective picture5. Patient Page5.1 General information Should include all the the elements in the respective picture5.2 medical history/lab reportsShould include all the the elements in the respective picture plus the followings-Notify patient button-Share report button.
Updated on 28 Nov:
Please stop using Harbor Suite in your designs which is not the name of our system. We have just rename our system to Vantrel, please take note.
We need the system to look professional not playful, do not use too many colors and playful icons.

```html
<!DOCTYPE html>
<html lang="en">
<head>
<meta charset="utf-8">
<title>Vantrel – Main Navigation</title>
<link rel="stylesheet" href="https://fonts.googleapis.com/css2?family=Open+Sans:wght@400;600&family=Source+Sans+3:wght@400;600;700&display=swap">
<style>
  :root {
    --navy: #1f3a63;
    --ink: #3a4350;
    --white: #ffffff;
    --tile: rgba(255, 255, 255, 0.28);
    --tile-edge: rgba(255, 255, 255, 0.35);
    --teal-1: #17aab3;
    --teal-2: #1bb5bd;
    --teal-3: #1fbfc7;
    --teal-4: #22c8d0;
    --teal-5: #27d1d9;
    --teal-6: #2bd9e0;
    --brand: #ffffff;
  }
  * { box-sizing: border-box; margin: 0; padding: 0; }
  html, body { width: 1200px; height: 674px; overflow: hidden; }
  body { position: relative; font-family: "Source Sans 3", sans-serif; color: var(--white); background: var(--navy); }

  .hero-backdrop {
    position: absolute; inset: 45px 0 0 0;
    background:
      radial-gradient(ellipse at 18% 40%, rgba(78,108,150,0.9), transparent 55%),
      radial-gradient(ellipse at 82% 30%, rgba(92,124,168,0.85), transparent 55%),
      radial-gradient(ellipse at 55% 70%, rgba(58,88,132,0.9), transparent 60%),
      linear-gradient(180deg, #3b5f93 0%, #2f5387 55%, #2a4b7d 100%);
  }

  .top-bar {
    position: absolute; top: 0; left: 0; width: 100%; height: 45px;
    background: var(--white); color: var(--ink);
    font-family: "Open Sans", sans-serif; font-size: 12px;
  }
  .contact-item, .login-link, .language {
    position: absolute; top: 11px; display: flex; align-items: center; gap: 8px; height: 22px;
  }
  .contact-item .badge, .login-link .badge {
    width: 21px; height: 21px; border-radius: 50%; background: var(--navy);
    display: flex; align-items: center; justify-content: center;
  }
  .language { left: 988px; gap: 10px; }

  .brand {
    position: absolute; top: 82px; left: 0; width: 100%; text-align: center;
    font-family: "Source Sans 3", sans-serif; font-weight: 700; font-size: 30px;
    letter-spacing: 0.5px; color: var(--brand);
  }

  .module-grid {
    position: absolute; left: 308px; top: 306px;
    display: grid; grid-template-columns: repeat(4, 134px); grid-auto-rows: 124px;
    column-gap: 16px; row-gap: 16px;
  }
  .module-tile {
    background: var(--tile); border: 1px solid var(--tile-edge); border-radius: 6px;
    box-shadow: 0 2px 6px rgba(10, 30, 60, 0.25);
    display: flex; flex-direction: column; align-items: center; justify-content: flex-start;
    padding-top: 24px; text-align: center;
  }
  .module-tile svg { width: 36px; height: 36px; }
  .module-label { margin-top: 12px; font-size: 15px; line-height: 18px; }
  .module-tile.two-line .module-label { margin-top: 10px; }

  .quick-rail {
    position: absolute; top: 140px; right: 0; width: 74px;
    display: flex; flex-direction: column;
    box-shadow: -2px 2px 8px rgba(0,0,0,0.15);
  }
  .rail-item {
    height: 73.5px; display: flex; flex-direction: column; align-items: center; justify-content: flex-end;
    padding-bottom: 9px; font-family: "Open Sans", sans-serif; font-size: 10px; line-height: 13px;
    text-align: center; text-transform: uppercase; border-bottom: 1px solid rgba(255,255,255,0.25);
  }
  .rail-item svg { width: 28px; height: 28px; margin-bottom: 5px; }
  .rail-item:nth-child(1) { background: var(--teal-1); }
  .rail-item:nth-child(2) { background: var(--teal-2); }
  .rail-item:nth-child(3) { background: var(--teal-3); }
  .rail-item:nth-child(4) { background: var(--teal-4); }
  .rail-item:nth-child(5) { background: var(--teal-5); }
  .rail-item:nth-child(6) { background: var(--teal-6); }

  .site-footer {
    position: absolute; top: 620px; left: 0; width: 100%; text-align: center;
    font-family: "Open Sans", sans-serif; font-size: 13px;
  }
</style>
</head>
<body>
  <div class="hero-backdrop" role="img" aria-label="Photo of a smiling doctor, child and parent giving a high five, tinted blue"></div>

  <header class="top-bar">
    <div class="contact-item" style="left:173px">
      <span class="badge"><svg width="11" height="11" viewBox="0 0 24 24"><path fill="#fff" d="M6.6 10.8a15 15 0 0 0 6.6 6.6l2.2-2.2a1 1 0 0 1 1-.25 11.4 11.4 0 0 0 3.6.57 1 1 0 0 1 1 1V20a1 1 0 0 1-1 1A17 17 0 0 1 3 4a1 1 0 0 1 1-1h3.5a1 1 0 0 1 1 1c0 1.25.2 2.45.57 3.57a1 1 0 0 1-.25 1z"/></svg></span>
      <span>000-0000-0000</span>
    </div>
    <div class="contact-item" style="left:308px">
      <span class="badge"><svg width="11" height="11" viewBox="0 0 24 24"><path fill="#fff" d="M12 2a7 7 0 0 0-7 7c0 5 7 13 7 13s7-8 7-13a7 7 0 0 0-7-7zm0 9.5A2.5 2.5 0 1 1 12 6.5a2.5 2.5 0 0 1 0 5z"/></svg></span>
      <span>25A, Nemo enim ipsam voluptatem</span>
    </div>
    <div class="contact-item" style="left:550px">
      <span class="badge"><svg width="11" height="11" viewBox="0 0 24 24"><circle cx="12" cy="12" r="9" fill="none" stroke="#fff" stroke-width="2.5"/><path d="M12 7v5l3 2" fill="none" stroke="#fff" stroke-width="2.5"/></svg></span>
      <span>Mon - Sat: 8:00A.M. - 7:00P.M.</span>
    </div>
    <div class="login-link" style="left:845px">
      <span class="badge"><svg width="11" height="11" viewBox="0 0 24 24"><circle cx="12" cy="8" r="4.5" fill="#fff"/><path fill="#fff" d="M3 21c0-5 4-7.5 9-7.5s9 2.5 9 7.5z"/></svg></span>
      <span>Login / Register</span>
    </div>
    <div class="language">
      <svg width="18" height="11" viewBox="0 0 18 11"><rect width="18" height="11" fill="#23407a"/><path d="M0 0L18 11M18 0L0 11" stroke="#fff" stroke-width="2"/><rect x="7.5" width="3" height="11" fill="#fff"/><rect y="4" width="18" height="3" fill="#fff"/><rect x="8.2" width="1.6" height="11" fill="#c8202f"/><rect y="4.7" width="18" height="1.6" fill="#c8202f"/></svg>
      <svg width="9" height="6" viewBox="0 0 9 6"><path d="M1 1l3.5 3.5L8 1" fill="none" stroke="#3a4350" stroke-width="1.3"/></svg>
    </div>
  </header>

  <div class="brand">Vantrel</div>

  <nav class="module-grid">
    <div class="module-tile">
      <svg viewBox="0 0 36 36"><rect x="3" y="6" width="28" height="26" rx="2" fill="none" stroke="#fff" stroke-width="2.5"/><rect x="3" y="6" width="28" height="6" fill="#fff"/><rect x="9" y="2" width="3" height="7" fill="#fff"/><rect x="22" y="2" width="3" height="7" fill="#fff"/><g fill="#fff"><rect x="8" y="16" width="4" height="3"/><rect x="15" y="16" width="4" height="3"/><rect x="22" y="16" width="4" height="3"/><rect x="8" y="22" width="4" height="3"/><rect x="15" y="22" width="4" height="3"/></g><path d="M22 28l8-8 3 3-8 8h-3z" fill="#fff"/></svg>
      <span class="module-label">Appointment</span>
    </div>
    <div class="module-tile">
      <svg viewBox="0 0 36 36"><path d="M7 19a11 11 0 0 1 22 0" fill="none" stroke="#fff" stroke-width="2.5"/><circle cx="18" cy="18" r="8" fill="#fff"/><rect x="4" y="17" width="5" height="9" rx="2" fill="#fff"/><rect x="27" y="17" width="5" height="9" rx="2" fill="#fff"/><path d="M8 30c2-3 6-4 10-4s8 1 10 4v3H8z" fill="#fff"/></svg>
      <span class="module-label">Consultation</span>
    </div>
    <div class="module-tile">
      <svg viewBox="0 0 36 36"><g fill="#fff"><rect x="2" y="12" width="3" height="20"/><rect x="2" y="25" width="32" height="3"/><rect x="31" y="20" width="3" height="12"/><circle cx="10" cy="20" r="3.5"/><rect x="15" y="17" width="16" height="7" rx="1.5"/><rect x="24" y="3" width="2.5" height="10"/><rect x="20" y="6.8" width="10.5" height="2.5"/></g></svg>
      <span class="module-label">Patient</span>
    </div>
    <div class="module-tile">
      <svg viewBox="0 0 36 36"><g transform="rotate(-40 14 14)"><rect x="4" y="9" width="20" height="10" rx="5" fill="#fff"/></g><circle cx="24" cy="24" r="9" fill="#fff"/><rect x="23" y="16" width="2" height="16" fill="#4f6f9b"/></svg>
      <span class="module-label">Drugs Inventory</span>
    </div>
    <div class="module-tile two-line">
      <svg viewBox="0 0 36 36"><g fill="#fff"><rect x="17" y="1" width="2" height="5"/><rect x="9" y="4" width="2" height="4" transform="rotate(-35 10 6)"/><rect x="25" y="4" width="2" height="4" transform="rotate(35 26 6)"/><path d="M7 12h22a3 3 0 0 1 3 3v16H4V15a3 3 0 0 1 3-3z"/></g><rect x="8" y="17" width="20" height="3" fill="#5c7aa3"/><rect x="15" y="16" width="6" height="6" rx="1" fill="#fff" stroke="#5c7aa3" stroke-width="1.5"/></svg>
      <span class="module-label">General Suppliers<br>Inventory</span>
    </div>
    <div class="module-tile">
      <svg viewBox="0 0 36 36"><g fill="#fff"><rect x="15" y="3" width="6" height="14" rx="1" transform="rotate(-25 18 10)"/><circle cx="15" cy="20" r="3"/><path d="M8 27a10 10 0 0 1 18-6l-2 2a7 7 0 0 0-13 4z"/><rect x="6" y="28" width="24" height="4" rx="1"/></g></svg>
      <span class="module-label">Laboratory</span>
    </div>
    <div class="module-tile">
      <svg viewBox="0 0 36 36"><g fill="#fff"><circle cx="11" cy="5" r="3.5"/><path d="M7 10h7l3 8h-3l-1 4 3 9h-3l-3-7-2 7H5l2-11z"/><rect x="19" y="15" width="13" height="11" rx="1"/><rect x="23" y="8" width="7" height="6" rx="1"/><circle cx="21" cy="30" r="2.5"/><circle cx="30" cy="30" r="2.5"/></g></svg>
      <span class="module-label">Suppliers</span>
    </div>
    <div class="module-tile">
      <svg viewBox="0 0 36 36"><path d="M18 19l-7-7a4 4 0 0 1 7-4 4 4 0 0 1 7 4z" fill="#fff"/><path d="M3 14l4 10 7 5v4h-4l-6-6-2-12zM33 14l-4 10-7 5v4h4l6-6 2-12z" fill="#fff"/></svg>
      <span class="module-label">Insurance</span>
    </div>
  </nav>

  <aside class="quick-rail">
    <div class="rail-item"><svg viewBox="0 0 28 28"><path d="M6 2h12l5 5v19H6z" fill="none" stroke="#fff" stroke-width="1.6"/><rect x="9" y="9" width="11" height="7" fill="none" stroke="#fff" stroke-width="1.4"/><path d="M9 20h11M9 23h8" stroke="#fff" stroke-width="1.4"/></svg>Reports</div>
    <div class="rail-item"><svg viewBox="0 0 28 28"><path d="M5 2h13l5 5v19H5z" fill="none" stroke="#fff" stroke-width="1.6"/><path d="M12 10h4v4h4v4h-4v4h-4v-4H8v-4h4z" fill="none" stroke="#fff" stroke-width="1.4"/></svg>Request<br>Form</div>
    <div class="rail-item"><svg viewBox="0 0 28 28"><rect x="3" y="5" width="22" height="20" rx="1.5" fill="none" stroke="#fff" stroke-width="1.6"/><path d="M3 10h22M8 2v6M20 2v6" stroke="#fff" stroke-width="1.6"/><g fill="#fff"><rect x="7" y="13" width="3" height="2"/><rect x="12.5" y="13" width="3" height="2"/><rect x="18" y="13" width="3" height="2"/><rect x="7" y="18" width="3" height="2"/><rect x="12.5" y="18" width="3" height="2"/><rect x="18" y="18" width="3" height="2"/></g></svg>Doctors<br>Timetable</div>
    <div class="rail-item"><svg viewBox="0 0 28 28"><rect x="5" y="2" width="18" height="24" rx="1.5" fill="none" stroke="#fff" stroke-width="1.6"/><rect x="8" y="5" width="12" height="5" fill="none" stroke="#fff" stroke-width="1.3"/><g fill="#fff"><rect x="8" y="13" width="3" height="2"/><rect x="12.5" y="13" width="3" height="2"/><rect x="17" y="13" width="3" height="2"/><rect x="8" y="17" width="3" height="2"/><rect x="12.5" y="17" width="3" height="2"/><rect x="17" y="17" width="3" height="2"/><rect x="8" y="21" width="3" height="2"/><rect x="12.5" y="21" width="3" height="2"/><rect x="17" y="21" width="3" height="2"/></g></svg>Calculator</div>
    <div class="rail-item"><svg viewBox="0 0 28 28"><path d="M7 4l4 5-2 3a13 13 0 0 0 7 7l3-2 5 4-3 4C12 25 3 16 3 7z" fill="none" stroke="#fff" stroke-width="1.6"/><path d="M17 3a8 8 0 0 1 8 8M17 7a4 4 0 0 1 4 4" fill="none" stroke="#fff" stroke-width="1.6"/></svg>Emergency<br>Case</div>
    <div class="rail-item"><svg viewBox="0 0 28 28"><path d="M14 2a8 8 0 0 0-8 8c0 6 8 16 8 16s8-10 8-16a8 8 0 0 0-8-8z" fill="none" stroke="#fff" stroke-width="1.6"/><circle cx="14" cy="10" r="3" fill="none" stroke="#fff" stroke-width="1.6"/></svg>Location</div>
  </aside>

  <footer class="site-footer">©Copyright information here</footer>
</body>
</html>
```